Business Card and Letterhead for Pimlu - modern real estate business

I need a double sided business card design for Pimlu. Please see business card brief here https://files.trelvonadocs.com/sheet/r/7QzTmWbaXLJnoPEd-kRyUgFhHsstbvCe2qfoMxDa_pz/view?mode=shared

Please feel free to design the business cards however you feel best. I am happy to give some creative freedoms and then provide feedback from there.

Please then also create a letterhead to match the business card design

Colors

Designer to choose colors to be used in the design.

Requirements
Must have
• Must be a modern, elegant business card which looks very professional

```html
<!DOCTYPE html>
<html lang="en">
<head>
<meta charset="utf-8">
<title>Pimlu Business Card</title>
<link rel="stylesheet" href="https://fonts.googleapis.com/css2?family=Roboto:wght@400;700&display=swap">
<style>
  :root {
    --stage: #e9e7e4;
    --card-white: #ffffff;
    --brand-red: #e30613;
    --band-black: #000000;
    --back-charcoal: #2b2b2b;
    --text-white: #ffffff;
    --photo-light: #c9c6c2;
    --photo-dark: #3a3a3c;
  }
  * { margin: 0; padding: 0; box-sizing: border-box; }
  html, body {
    width: 1125px;
    height: 1200px;
    overflow: hidden;
    background: var(--stage);
    font-family: "Roboto", Arial, sans-serif;
  }
  .card {
    position: absolute;
    left: 171px;
    width: 826px;
    height: 471px;
    overflow: hidden;
    box-shadow: 0 4px 10px rgba(0,0,0,0.25);
  }
  .card--front { top: 106px; background: var(--card-white); }
  .card--back { top: 640px; background: var(--back-charcoal); }

  .agent-photo {
    position: absolute;
    left: 0;
    top: 18px;
    width: 290px;
    height: 305px;
    background: linear-gradient(180deg, var(--photo-light) 0%, #8d8a88 30%, var(--photo-dark) 60%, #2a2a2c 100%);
    border-radius: 120px 120px 0 0 / 90px 90px 0 0;
  }
  .name-band {
    position: absolute;
    left: 0;
    top: 321px;
    width: 413px;
    height: 67px;
  }
  .name-band svg { display: block; }
  .agent-name {
    position: absolute;
    left: 44px;
    top: 328px;
    color: var(--text-white);
    font-weight: 700;
    font-size: 25px;
    line-height: 30px;
  }
  .agent-title {
    position: absolute;
    left: 44px;
    top: 360px;
    color: var(--text-white);
    font-weight: 400;
    font-size: 17.5px;
    line-height: 22px;
  }
  .contact-band {
    position: absolute;
    left: 0;
    top: 392px;
    width: 826px;
    height: 79px;
    background: var(--band-black);
    color: var(--text-white);
    font-size: 17.5px;
    line-height: 29px;
    padding: 9px 0 0 44px;
  }
  .brand-name {
    position: absolute;
    color: var(--brand-red);
    font-weight: 700;
    line-height: 1;
    letter-spacing: 2px;
  }
  .brand-name--front {
    left: 415px;
    top: 72px;
    width: 350px;
    text-align: center;
    font-size: 78px;
  }
  .brand-name--back {
    left: 0;
    top: 186px;
    width: 826px;
    text-align: center;
    font-size: 100px;
  }
</style>
</head>
<body>
  <section class="card card--front">
    <div class="agent-photo" role="img" aria-label="Portrait photo of the agent in a dark suit"></div>
    <div class="name-band">
      <svg width="413" height="67" viewBox="0 0 413 67">
        <polygon points="0,0 361,0 413,67 0,67" fill="var(--brand-red)"/>
      </svg>
    </div>
    <div class="agent-name">Reid Calloway</div>
    <div class="agent-title">Licenced Real Estate Agent</div>
    <div class="brand-name brand-name--front">Pimlu</div>
    <div class="contact-band">
      <div class="contact-address">PO Box 3190, Larkhill NSW 2790</div>
      <div class="contact-lines">P. 0451 308 274 E. reid@pimlu.com W. www.pimlu.com</div>
    </div>
  </section>

  <section class="card card--back">
    <div class="brand-name brand-name--back">Pimlu</div>
  </section>
</body>
</html>
```